BrindleStaffing Business Card Design

We are a staffing company finding positions for dedicated nurses and physicians.

Target Market(s)

Business Professionals

Industry/Entity Type

Staffing

Contact Information for Business Card

Gordon Pratley
Chairman
417 39th Avenue South
SAINT PETERSBURG FL 33712
813-555-4172 Mobile
813-555-8036 Fax
gpratley@brindlestaffing.com
www.brindlestaffing.com

Font styles to use
Sans Serif

Colors
fbee3e
f04a50
f37122

Requirements
Must have
• Logo Attached, see colors below. We'd like to see Yellow, Orange and Red.

```html
<!DOCTYPE html>
<html lang="en">
<head>
<meta charset="utf-8">
<title>BrindleStaffing Business Card</title>
<link rel="stylesheet" href="https://fonts.googleapis.com/css2?family=Open+Sans:wght@400;600;700&display=swap">
<style>
  :root {
    --backdrop-light: #8e8f91;
    --backdrop-dark: #3c3b3c;
    --brand-orange: #f37122;
    --brand-red: #f04a50;
    --brand-yellow: #fbee3e;
    --cross-tint: #fef8d2;
    --paper: #ffffff;
    --ink: #222222;
  }
  html, body {
    margin: 0;
    width: 1200px;
    height: 1135px;
    overflow: hidden;
  }
  body {
    position: relative;
    background: radial-gradient(circle at 50% 50%, var(--backdrop-light) 0%, var(--backdrop-dark) 85%);
    font-family: "Open Sans", Arial, sans-serif;
  }
  .card {
    position: absolute;
    width: 717px;
    height: 410px;
    border-radius: 38px;
    overflow: hidden;
  }
  .card-front {
    left: 368px;
    top: 110px;
    background: var(--brand-orange);
  }
  .card-back {
    left: 99px;
    top: 590px;
    background: var(--paper);
  }
  .front-shape {
    position: absolute;
    inset: 0;
    width: 100%;
    height: 100%;
  }
  .wordmark {
    position: absolute;
    display: flex;
    align-items: center;
    font-weight: 700;
    color: var(--brand-red);
    letter-spacing: -0.5px;
    white-space: nowrap;
  }
  .wordmark-dot {
    border-radius: 50%;
    background: var(--brand-orange);
  }
  .card-front .wordmark {
    left: 26px;
    top: 188px;
    font-size: 38px;
    gap: 8px;
  }
  .card-front .wordmark-dot { width: 14px; height: 14px; }
  .contact {
    position: absolute;
    right: 21px;
    color: var(--paper);
    text-align: right;
  }
  .holder { top: 48px; }
  .holder-name {
    margin: 0;
    font-size: 23px;
    font-weight: 700;
    line-height: 30px;
  }
  .holder-title {
    margin: 0;
    font-size: 21px;
    line-height: 26px;
  }
  .address {
    top: 206px;
    font-size: 18px;
    line-height: 28px;
  }
  .address p { margin: 0; }
  .lines {
    top: 310px;
    font-size: 18px;
    list-style: none;
    margin: 0;
    padding: 0;
  }
  .lines li {
    display: flex;
    justify-content: flex-end;
    align-items: center;
    gap: 8px;
    height: 30px;
  }
  .lines svg { width: 17px; height: 17px; }
  .cross-vertical {
    position: absolute;
    left: 288px;
    top: 0;
    width: 164px;
    height: 410px;
    background: var(--cross-tint);
  }
  .cross-horizontal {
    position: absolute;
    left: 165px;
    top: 123px;
    width: 409px;
    height: 164px;
    background: var(--cross-tint);
  }
  .card-back .wordmark {
    left: 0;
    right: 0;
    top: 160px;
    justify-content: center;
    font-size: 54px;
    gap: 12px;
  }
  .card-back .wordmark-dot { width: 18px; height: 18px; }
  .back-web {
    position: absolute;
    left: 0;
    right: 0;
    top: 258px;
    margin: 0;
    text-align: center;
    font-size: 22px;
    letter-spacing: 2px;
    color: var(--ink);
  }
  .back-web .domain {
    color: var(--brand-red);
    font-weight: 600;
  }
</style>
</head>
<body>

<section class="card card-front">
  <svg class="front-shape" viewBox="0 0 746 426" preserveAspectRatio="none" aria-hidden="true">
    <path d="M0,162 C50,90 100,35 145,0 L550,0 C520,170 430,340 240,395 C150,418 60,405 0,382 Z" fill="var(--brand-red)"/>
    <path d="M0,180 C60,100 110,40 170,0 L500,0 C495,150 400,330 220,388 C140,410 60,395 0,372 Z" fill="var(--paper)"/>
  </svg>

  <div class="wordmark"><span class="wordmark-dot"></span>BrindleStaffing</div>

  <div class="contact holder">
    <p class="holder-name">Gordon Pratley</p>
    <p class="holder-title">Chairman</p>
  </div>

  <div class="contact address">
    <p>417 39th Avenue South</p>
    <p>Saint petersburg fl 33712</p>
  </div>

  <ul class="contact lines">
    <li>813-555-4172
      <svg viewBox="0 0 20 20" aria-hidden="true"><circle cx="10" cy="10" r="8.5" fill="none" stroke="currentColor" stroke-width="1.6"/><path d="M7.5,5.5 L9,8 L8,9 C8.6,10.4 9.6,11.4 11,12 L12,11 L14.5,12.5 L13.5,14.5 C9.5,14.5 5.5,10.5 5.5,6.5 Z" fill="currentColor"/></svg>
    </li>
    <li>gpratley@brindlestaffing.com
      <svg viewBox="0 0 20 20" aria-hidden="true"><path d="M2,8 L10,3 L18,8 L18,17 L2,17 Z" fill="currentColor"/><path d="M2,8 L10,13 L18,8" fill="none" stroke="var(--brand-orange)" stroke-width="1.5"/></svg>
    </li>
    <li>www.brindlestaffing.com
      <svg viewBox="0 0 20 20" aria-hidden="true" fill="none" stroke="currentColor" stroke-width="1.3"><circle cx="10" cy="10" r="8.5"/><ellipse cx="10" cy="10" rx="3.8" ry="8.5"/><path d="M1.5,10 H18.5 M3,5.5 H17 M3,14.5 H17"/></svg>
    </li>
  </ul>
</section>

<section class="card card-back">
  <div class="cross-vertical"></div>
  <div class="cross-horizontal"></div>
  <div class="wordmark"><span class="wordmark-dot"></span>BrindleStaffing</div>
  <p class="back-web">www.<span class="domain">brindlestaffing</span>.com</p>
</section>

</body>
</html>
```